Business Cards for company that supports physicians that do medical research

Need to create a business card for Qorvel Studies (www.qorvelstudies.example), a company devoted to supporting physicians who conduct medical research. The form of the card should match the message of research and information quest. I have provided the logo of the company as an uploaded file. Designs should be simple and slick aimed at very high end clients.

Target Market(s)

Medical doctors that are also researchers

Industry/Entity Type

Medical

Contact Information for Business Card

Should feature logo and fields for personal info:
Name/title
Phone /email

Font styles to use
Serif
Sans Serif

Requirements
Must have
• Qorvel logo and fields for personal info:
• Name: Bertrand Okonfu
• Title: VP Research and Senior Analyst
• Phone: 555-203-4719
• email: info@qorvelstudies.example
Nice to have
• Interesting cards that I've seen:
• 1- all black/charcoal or very dark background
• 2- Plastic - semi-transparent
• 3- non-standard height-width ratios
• 4- Functional cards -- USB drive incorporated
Should not have
• Too busy; needs to stay very simple

```html
<!DOCTYPE html>
<html lang="en">
<head>
<meta charset="utf-8">
<title>Qorvel Studies – Business Card</title>
<link rel="stylesheet" href="https://fonts.googleapis.com/css2?family=Open+Sans:wght@400;600&display=swap">
<style>
  :root {
    --page-bg: #e9e6e2;
    --card-bg: #262626;
    --card-edge: #3a3a3a;
    --brand-grey: #c8c8c8;
    --accent-blue: #2a8ad4;
    --accent-green: #4cbc4a;
    --text-white: #f4f4f4;
  }
  * { box-sizing: border-box; margin: 0; padding: 0; }
  html, body {
    width: 1200px;
    height: 900px;
    overflow: hidden;
    background: var(--page-bg);
    font-family: "Open Sans", Arial, sans-serif;
  }
  .business-card {
    position: absolute;
    left: 145px;
    top: 170px;
    width: 910px;
    height: 560px;
    border-radius: 26px;
    background: linear-gradient(160deg, #2e2e2e 0%, var(--card-bg) 55%, #1f1f1f 100%);
    border: 2px solid var(--card-edge);
    box-shadow: 0 18px 40px rgba(0,0,0,0.25);
  }
  .brand {
    position: absolute;
    left: 48px;
    top: 110px;
    display: flex;
    align-items: center;
    gap: 22px;
  }
  .brand-dot {
    width: 46px;
    height: 46px;
    border-radius: 50%;
    background: var(--accent-green);
  }
  .brand-name {
    font-size: 64px;
    font-weight: 600;
    color: var(--brand-grey);
    letter-spacing: 1px;
    line-height: 1;
  }
  .person {
    position: absolute;
    right: 49px;
    top: 295px;
    text-align: right;
  }
  .person-name {
    font-size: 31px;
    font-weight: 600;
    color: var(--accent-blue);
    line-height: 1.3;
  }
  .person-title {
    font-size: 24px;
    font-weight: 400;
    color: var(--text-white);
    line-height: 1.5;
  }
  .contact {
    position: absolute;
    right: 49px;
    top: 425px;
    list-style: none;
    text-align: right;
  }
  .contact-item {
    display: flex;
    justify-content: flex-end;
    align-items: center;
    gap: 14px;
    font-size: 23px;
    color: var(--text-white);
    height: 38px;
  }
  .contact-icon {
    width: 26px;
    height: 26px;
    flex: none;
  }
</style>
</head>
<body>
  <main class="business-card">
    <div class="brand">
      <span class="brand-dot"></span>
      <span class="brand-name">Qorvel Studies</span>
    </div>

    <div class="person">
      <p class="person-name">Bertrand Okonfu</p>
      <p class="person-title">VP Research and Senior Analyst</p>
    </div>

    <ul class="contact">
      <li class="contact-item">
        <span>555-203-4719</span>
        <svg class="contact-icon" viewBox="0 0 26 26" aria-hidden="true">
          <rect width="26" height="26" rx="4" fill="#2a8ad4"/>
          <path d="M6 11c0-3 3-4 7-4s7 1 7 4l-3 1-1-2h-6l-1 2z" fill="#fff"/>
          <rect x="8" y="13" width="10" height="6" rx="1.5" fill="#fff"/>
        </svg>
      </li>
      <li class="contact-item">
        <span>info@qorvelstudies.example</span>
        <svg class="contact-icon" viewBox="0 0 26 26" aria-hidden="true">
          <rect width="26" height="26" rx="4" fill="#2a8ad4"/>
          <rect x="6" y="8" width="14" height="10" rx="1" fill="#fff"/>
          <path d="M6 8.5l7 5.5 7-5.5" fill="none" stroke="#2a8ad4" stroke-width="1.4"/>
        </svg>
      </li>
    </ul>
  </main>
</body>
</html>
```